NZ First of it's kind solutions directory and marketplace for busy Mums needs a business card design

We need a business card design for our new nationwide business in NZ (long term plans to go global). We provide solutions to the everyday challenges that busy Mums face by connecting them with quality communities and suppliers of carefully selected, relevant products and services. We sell direct via our online marketplace. The final design should communicate our values of inclusivity, quality and smart solutions. Colours should incorporate our logo colour palette of #477077 and #6ba8b2. Our website is at https://www.brightnestmums.example

Target Market(s)

busy Mums, Age 28 – 50, female, income over $100K, location main centres NZ primarily but NZ wide. Is likely juggling work or career with a young family. Probably had hobbies which have fallen by the wayside.
-Wants to succeed in her chosen career without compromising on family life
-to successfully juggle her career without feeling like she is compromising her children
- Is time poor, something always has to give and it’s generally her health (she’ll stay up late, get stressed)
- probably ex corporate or professional career. Has discretional income

Industry/Entity Type

Business

Contact Information for Business Card

Lena Forbisher, Founder, BrightNestMums.example (Strapline Tap; Gather; Sorted), 47 Kowhai Terrace, Ellerslie, Auckland 1051, New Zealand. Mob: 021 483 517 Ph: +64 (0)9 571 4860

Font styles to use
Other font styles liked:
• Raleway, and/or Architects Daughter

Colors
00a990
33b8a4
86cfc6
cfeae6

Requirements
Must have
• the above details, streamline. the logo and colours associated with those logos
Should not have
• foil or metallic colours

```html
<!DOCTYPE html>
<html lang="en">
<head>
<meta charset="utf-8">
<title>BrightNest Mums – Business Card</title>
<link href="https://fonts.googleapis.com/css2?family=Roboto:ital,wght@0,400;0,500;0,700;1,400&display=swap" rel="stylesheet">
<style>
  :root {
    --stage: #e8e8e8;
    --teal-deep: #3e5f67;
    --teal-brand: #477077;
    --teal-light: #6ba8b2;
    --ink: #3a3a3a;
    --paper: #f7f7f6;
    --white: #ffffff;
  }
  * { box-sizing: border-box; margin: 0; padding: 0; }
  html, body { width: 1200px; height: 576px; overflow: hidden; }
  body {
    background: var(--stage);
    font-family: "Roboto", Arial, sans-serif;
    position: relative;
  }
  .card {
    position: absolute;
    top: 138px;
    width: 484px;
    height: 292px;
    border-radius: 12px;
    overflow: hidden;
    box-shadow: 0 3px 8px rgba(0,0,0,0.18);
  }
  /* Back of card */
  .card-back {
    left: 82px;
    background: linear-gradient(180deg, #466a72 0%, var(--teal-deep) 100%);
    color: var(--white);
    text-align: center;
  }
  .card-back .brand-name {
    position: absolute;
    left: 0; right: 0;
    top: 108px;
    font-size: 42px;
    font-weight: 700;
    letter-spacing: -0.5px;
    color: var(--white);
  }
  .card-back .strapline {
    position: absolute;
    left: 0; right: 0;
    top: 170px;
    font-size: 15px;
    letter-spacing: 5.5px;
    color: var(--white);
  }
  /* Front of card */
  .card-front {
    left: 602px;
    background: var(--paper);
    color: var(--ink);
  }
  .card-front .brand-name {
    position: absolute;
    left: 26px;
    top: 32px;
    font-size: 31px;
    font-weight: 700;
    letter-spacing: -0.6px;
    color: var(--teal-brand);
  }
  .card-front .strapline {
    position: absolute;
    left: 27px;
    top: 73px;
    font-size: 11px;
    letter-spacing: 3.6px;
    color: var(--ink);
  }
  .strapline .divider { color: var(--teal-light); }
  .address {
    position: absolute;
    left: 26px;
    top: 160px;
    font-size: 12.5px;
    line-height: 18px;
    font-style: normal;
  }
  .contact-list {
    position: absolute;
    left: 26px;
    top: 206px;
    list-style: none;
    font-size: 12.5px;
  }
  .contact-list li {
    display: flex;
    align-items: center;
    height: 18.3px;
  }
  .contact-list svg {
    width: 10px; height: 10px;
    margin-right: 8px;
    fill: var(--teal-light);
    flex-shrink: 0;
  }
  .name-disc {
    position: absolute;
    left: 278px;
    top: 96px;
    width: 204px;
    height: 204px;
    border-radius: 50%;
    background: var(--teal-deep);
  }
  .person {
    position: absolute;
    left: 278px;
    width: 204px;
    top: 213px;
    text-align: center;
    color: var(--white);
  }
  .person .name { font-size: 19px; font-weight: 700; }
  .person .role { font-size: 11.5px; font-style: italic; margin-top: 2px; }
</style>
</head>
<body>

<section class="card card-back" aria-label="Card back">
  <div class="brand-name">BrightNest Mums</div>
  <div class="strapline">TAP <span class="divider">|</span> GATHER <span class="divider">|</span> SORTED</div>
</section>

<section class="card card-front" aria-label="Card front">
  <div class="brand-name">BrightNestMums</div>
  <div class="strapline">TAP <span class="divider">|</span> GATHER <span class="divider">|</span> SORTED</div>

  <address class="address">
    47 Kowhai Terrace, Ellerslie,<br>
    Auckland 1051, New Zealand
  </address>

  <ul class="contact-list">
    <li>
      <svg viewBox="0 0 10 10" aria-hidden="true"><rect x="2.5" y="0.5" width="5" height="9" rx="1"/><rect x="3.5" y="1.5" width="3" height="6" fill="#f7f7f6"/></svg>
      021 483 517
    </li>
    <li>
      <svg viewBox="0 0 10 10" aria-hidden="true"><path d="M0.5 3.5 Q5 0 9.5 3.5 L8.5 5 L7 4.2 L7 3.3 Q5 2.5 3 3.3 L3 4.2 L1.5 5 Z"/><rect x="2" y="5" width="6" height="4" rx="0.8"/></svg>
      +64 (0)9 571 4860
    </li>
    <li>
      <svg viewBox="0 0 10 10" aria-hidden="true"><rect x="0.5" y="2" width="9" height="6"/><path d="M0.5 2 L5 5.5 L9.5 2" fill="none" stroke="#f7f7f6" stroke-width="0.9"/></svg>
      www.BrightNestMums.example
    </li>
    <li>
      <svg viewBox="0 0 10 10" aria-hidden="true"><circle cx="5" cy="5" r="4.5"/><path d="M0.5 5 H9.5 M5 0.5 V9.5 M5 0.5 Q2 5 5 9.5 M5 0.5 Q8 5 5 9.5" fill="none" stroke="#f7f7f6" stroke-width="0.7"/></svg>
      lena@brightnestmums.example
    </li>
  </ul>

  <div class="name-disc"></div>
  <div class="person">
    <div class="name">Lena Forbisher</div>
    <div class="role">Founder</div>
  </div>
</section>

</body>
</html>
```